Business cards to launch an education platform

Hi,
I am looking at having new business cards designed.
I am a startup, developing a web platform for schools and university, the education world. It's an online assessment system.
I would like a card that looks classy, and that is using the colors and the font of my logo.

I have attached:
1) my logo
2) A business card that I have designed quickly so you can have all the information required in the card, but I really don't like it.
3) The font that I am using (Lato Regular) to design my web platform
4) Some screenshots of my web platform so you can have a look at the style that I have.

Target Market(s)

Major market: Education system: Schools and university
Minor markets: Business in general

Industry/Entity Type

Business

Contact Information for Business Card

Clara Fenwick
Director

M: 0437 518 902
E: clara.fenwick@amberLoomSystems.com.au

Requirements
Must have
• The colors of my logo

```html
<!DOCTYPE html>
<html lang="en">
<head>
<meta charset="utf-8">
<title>Amber Loom Systems – Business Card</title>
<link href="https://fonts.googleapis.com/css2?family=Lato:wght@400;700&display=swap" rel="stylesheet">
<style>
  :root {
    --backdrop: #141414;
    --card-white: #ffffff;
    --brand-navy: #163a66;
    --brand-blue: #1b7cc6;
    --band-top: #2a9de0;
    --band-bottom: #1a6fc0;
    --ink: #1c1c1c;
    --back-light: #2c9fdc;
    --back-dark: #1b6bba;
    --back-mark: rgba(255, 255, 255, 0.22);
  }
  * { margin: 0; padding: 0; box-sizing: border-box; }
  html, body { width: 1200px; height: 900px; overflow: hidden; }
  body {
    background: var(--backdrop);
    font-family: "Lato", sans-serif;
    position: relative;
  }
  .card {
    position: absolute;
    top: 170px;
    width: 347px;
    height: 561px;
  }
  .card-front { left: 259px; background: var(--card-white); }
  .card-back {
    left: 631px;
    background: linear-gradient(180deg, var(--back-light) 0%, var(--back-dark) 100%);
  }
  .accent-band {
    position: absolute;
    left: 102px;
    width: 143px;
    height: 30px;
    background: linear-gradient(180deg, var(--band-top), var(--band-bottom));
  }
  .accent-band.top { top: 0; }
  .accent-band.bottom { bottom: 0; height: 28px; }

  .brand {
    position: absolute;
    top: 108px;
    left: 0;
    width: 100%;
    text-align: center;
  }
  .brand-square {
    display: block;
    width: 70px;
    height: 70px;
    margin: 0 auto 40px;
    background: var(--brand-navy);
  }
  .brand-name {
    font-size: 27px;
    font-weight: 400;
    letter-spacing: 2px;
    color: var(--brand-navy);
    line-height: 1.1;
  }

  .contact {
    position: absolute;
    top: 350px;
    left: 0;
    width: 100%;
    text-align: center;
    color: var(--ink);
  }
  .person-name {
    font-size: 22px;
    color: var(--brand-blue);
    line-height: 1.3;
  }
  .person-role {
    font-size: 16px;
    line-height: 1.3;
    margin-bottom: 20px;
  }
  .contact-line {
    font-size: 16px;
    line-height: 20px;
    white-space: nowrap;
  }
  .contact-line svg {
    vertical-align: -1px;
    margin-right: 5px;
    fill: var(--brand-blue);
  }

  .back-name {
    position: absolute;
    top: 50%;
    left: 0;
    width: 100%;
    transform: translateY(-50%);
    text-align: center;
    font-size: 30px;
    font-weight: 700;
    letter-spacing: 2px;
    color: var(--back-mark);
  }
</style>
</head>
<body>
  <section class="card card-front">
    <div class="accent-band top"></div>
    <div class="brand">
      <span class="brand-square"></span>
      <p class="brand-name">AMBER LOOM<br>SYSTEMS</p>
    </div>
    <div class="contact">
      <p class="person-name">Clara Fenwick</p>
      <p class="person-role">Director</p>
      <p class="contact-line">
        <svg width="13" height="13" viewBox="0 0 24 24" aria-hidden="true"><path d="M6.6 10.8a15.1 15.1 0 0 0 6.6 6.6l2.2-2.2a1 1 0 0 1 1-.25 11.4 11.4 0 0 0 3.6.57 1 1 0 0 1 1 1V20a1 1 0 0 1-1 1A17 17 0 0 1 3 4a1 1 0 0 1 1-1h3.5a1 1 0 0 1 1 1c0 1.25.2 2.45.57 3.57a1 1 0 0 1-.25 1z"/></svg>0437 518 902
      </p>
      <p class="contact-line">
        <svg width="11" height="9" viewBox="0 0 22 16" aria-hidden="true"><path d="M0 0h22v16H0z M1.5 1.5 11 9l9.5-7.5" stroke="#fff" stroke-width="1.5"/></svg>clara.fenwick@amberLoomSystems.com.au
      </p>
    </div>
    <div class="accent-band bottom"></div>
  </section>

  <section class="card card-back">
    <p class="back-name">AMBER LOOM</p>
  </section>
</body>
</html>
```